Business Card for Coastal Tundrabridge Advisory

We need a business card for Coastal Tundrabridge Advisory. The company website address is provided below. The company logo is attached. We provide specialized permafrost services to the mining, transportation, and oil & gas industries. The card should be prepared for:
Matthias Korhonen, PhD.
Coastal Tundrabridge Advisory
PO Box 418259
Quillwater, Alaska 99642
Direct: +1-907-555-0143
Email: mkorhonen@tundrabridgeadvisory.example
Website: www.coastaltundrabridgeadvisory.example

```html
<!DOCTYPE html>
<html lang="en">
<head>
<meta charset="utf-8">
<title>Coastal Tundrabridge Advisory — Business Card</title>
<link rel="stylesheet" href="https://fonts.googleapis.com/css2?family=Quicksand:wght@400;500;600;700&display=swap">
<style>
  :root {
    --backdrop: #a9a9a9;
    --card-white: #ffffff;
    --ink: #3a3a3a;
    --ink-strong: #2b2b2b;
    --logo-white: #ffffff;
    --watermark: #ececec;
    --sky-top: #b7b3cc;
    --sky-pink: #e8909a;
    --sky-glow: #f7a06e;
    --horizon: #8f8f9c;
    --snow-dark: #6f7480;
    --snow-mid: #c9ccd4;
    --snow-light: #eef0f4;
  }
  * { margin: 0; padding: 0; box-sizing: border-box; }
  html, body { width: 1200px; height: 1000px; overflow: hidden; }
  body {
    background: var(--backdrop);
    font-family: "Quicksand", sans-serif;
    position: relative;
  }
  .card {
    position: absolute;
    width: 615px;
    height: 354px;
    overflow: hidden;
  }
  .card--front { left: 295px; top: 132px; }
  .card--back { left: 291px; top: 530px; background: var(--card-white); }

  .front-photo {
    position: absolute; inset: 0;
    background:
      radial-gradient(ellipse 75% 70% at 50% 50%, rgba(255,255,255,0) 60%, rgba(240,240,248,0.85) 100%),
      linear-gradient(to bottom,
        var(--sky-top) 0%,
        var(--sky-pink) 22%,
        var(--sky-glow) 34%,
        var(--horizon) 38%,
        var(--snow-dark) 52%,
        var(--snow-mid) 72%,
        var(--snow-light) 100%);
  }
  .front-brand {
    position: absolute;
    left: 0; right: 0; top: 152px;
    text-align: center;
    color: var(--logo-white);
    font-weight: 600;
    font-size: 27px;
    letter-spacing: 3px;
    text-transform: uppercase;
  }

  .contact {
    position: absolute;
    left: 0; right: 0; top: 65px;
    text-align: center;
    color: var(--ink);
    font-size: 15px;
    line-height: 19.5px;
  }
  .contact p + p { margin-top: 18px; }
  .contact__name { font-weight: 700; color: var(--ink-strong); letter-spacing: 0.3px; }
  .contact__web-name { font-weight: 600; color: var(--ink-strong); }
  .back-watermark {
    position: absolute;
    left: 0; right: 0; bottom: -14px;
    text-align: center;
    white-space: nowrap;
    color: var(--watermark);
    font-weight: 600;
    font-size: 54px;
    letter-spacing: 4px;
  }
</style>
</head>
<body>
  <section class="card card--front">
    <div class="front-photo" role="img" aria-label="Photograph of a snow-covered open-pit mine under a pink sunrise sky"></div>
    <div class="front-brand">Coastal Tundrabridge Advisory</div>
  </section>

  <section class="card card--back">
    <div class="contact">
      <p><span class="contact__name">MATTHIAS KORHONEN, PHD.</span><br>Coastal Tundrabridge Advisory</p>
      <p>PO Box 418259<br>Quillwater, Alaska 99642</p>
      <p>(907) 555-0143<br>mkorhonen@tundrabridgeadvisory.example</p>
      <p><span class="contact__web-name">coastaltundrabridgeadvisory</span>.example</p>
    </div>
    <div class="back-watermark" aria-hidden="true">COASTAL TUNDRABRIDGE</div>
  </section>
</body>
</html>
```